business card for horse saddlery

after a new business card for our saddlery, i will add 2 logos we have previously used and they can be used (or not) . Any images can be used from our website also at www.harrowfields.net.au, I have also added our brand logo, which may be good to incorporate on back ? we have over 15, 000 items online, ship Australia Wide.

Target Market(s)

horse owners

Industry/Entity Type

Retail - Equestrian

Contact Information for Business Card

Harrowfield Horse Supplies, 1300 48 62 90, www.harrowfields.net.au, 27 Lindqvist Rd Marrowbank Q 4587

Requirements
Must have
• trailgem is our brand so trailgem logo on back as 'distributers of', easy to read
Nice to have
• professional but fun
Should not have
• double sided (description wont save double sided)

```html
<!DOCTYPE html>
<html lang="en">
<head>
<meta charset="utf-8">
<title>Harrowfield Horse Supplies – Business Card</title>
<link href="https://fonts.googleapis.com/css2?family=Poppins:wght@400;500;600;700&display=swap" rel="stylesheet">
<style>
  :root {
    --backdrop: #8d8a85;
    --navy: #0a4179;
    --navy-deep: #083766;
    --royal: #1a52a0;
    --sky: #4fb4e8;
    --ink: #111111;
    --paper: #ffffff;
    --paper-shade: #eef0f3;
  }
  * { margin: 0; padding: 0; box-sizing: border-box; }
  html, body {
    width: 722px; height: 1200px; overflow: hidden;
    background: var(--backdrop);
    font-family: "Poppins", sans-serif;
  }
  .sheet {
    position: relative; width: 722px; height: 1200px;
    display: flex; justify-content: center; align-items: center; gap: 38px;
  }
  .card {
    position: relative; width: 320px; height: 561px; overflow: hidden;
    box-shadow: 0 10px 22px rgba(0,0,0,0.25);
  }
  .card svg.frame { position: absolute; inset: 0; }
  .card-back { background: var(--navy); }
  .card-front { background: linear-gradient(180deg, var(--paper) 0%, var(--paper-shade) 60%, var(--paper) 100%); }

  .photo-wash {
    position: absolute; left: 40px; top: 50px; width: 240px; height: 440px;
    background: radial-gradient(ellipse at 50% 40%, rgba(5,40,80,0.35), rgba(10,65,121,0) 70%);
  }
  .distributers {
    position: absolute; top: 146px; width: 100%; text-align: center;
    color: var(--sky); font-weight: 700; font-size: 15px; letter-spacing: 4.5px;
  }
  .brand-mark {
    position: absolute; top: 200px; width: 100%;
    display: flex; flex-direction: column; align-items: center; gap: 14px;
  }
  .brand-mark .dot { width: 54px; height: 54px; border-radius: 50%; background: var(--paper); }
  .brand-mark .name {
    color: var(--paper); font-weight: 500; font-size: 34px; letter-spacing: 1px; text-transform: uppercase;
  }
  .back-url {
    position: absolute; top: 490px; width: 100%; text-align: center;
    color: var(--paper); font-size: 12.5px; letter-spacing: 2.2px;
  }
  .back-url b { font-weight: 700; }

  .front-logo {
    position: absolute; top: 56px; left: 40px; width: 240px; height: 150px;
    display: flex; align-items: center; justify-content: center; gap: 10px;
    background: radial-gradient(ellipse at 50% 50%, rgba(79,180,232,0.18), rgba(79,180,232,0) 70%);
  }
  .front-logo .dot { width: 40px; height: 40px; border-radius: 50%; background: var(--sky); }
  .front-logo .name { color: var(--royal); font-weight: 500; font-size: 20px; }
  .business-name {
    position: absolute; top: 222px; width: 100%; text-align: center;
    color: var(--navy); font-weight: 700; font-size: 31px; letter-spacing: -0.5px;
  }
  .ribbon { position: absolute; top: 272px; left: 70px; width: 180px; height: 46px; }
  .ribbon-text {
    position: absolute; top: 280px; width: 100%; text-align: center;
    color: var(--sky); font-weight: 700; font-size: 12px;
  }
  .phone {
    position: absolute; top: 346px; width: 100%; text-align: center;
    color: var(--ink); font-weight: 700; font-size: 25px; letter-spacing: 0.5px;
  }
  .rule { position: absolute; left: 40px; width: 240px; height: 1.5px; background: var(--royal); }
  .rule-top { top: 384px; }
  .rule-bottom { top: 453px; }
  .contact, .address {
    position: absolute; width: 100%; text-align: center;
    color: var(--ink); font-size: 13.5px; line-height: 21px;
  }
  .contact { top: 398px; }
  .address { top: 464px; font-size: 13px; line-height: 19px; }
</style>
</head>
<body>
<main class="sheet">

  <section class="card card-back" aria-label="Card back">
    <div class="photo-wash" role="img" aria-label="Faint photo of a horse in the background"></div>
    <svg class="frame" width="320" height="561" viewBox="0 0 320 561" aria-hidden="true">
      <path d="M42 20 H278 A22 22 0 0 0 300 42 V519 A22 22 0 0 0 278 541 H42 A22 22 0 0 0 20 519 V42 A22 22 0 0 0 42 20 Z" fill="none" stroke="#ffffff" stroke-width="3"/>
      <path d="M44 26 H276 A18 18 0 0 0 294 44 V517 A18 18 0 0 0 276 535 H44 A18 18 0 0 0 26 517 V44 A18 18 0 0 0 44 26 Z" fill="none" stroke="#ffffff" stroke-width="1.2"/>
    </svg>
    <p class="distributers">DISTRIBUTERS OF</p>
    <div class="brand-mark">
      <span class="dot"></span>
      <span class="name">Trailgem</span>
    </div>
    <p class="back-url">www.<b>harrowfields</b>.net.au</p>
  </section>

  <section class="card card-front" aria-label="Card front">
    <svg class="frame" width="320" height="561" viewBox="0 0 320 561" aria-hidden="true">
      <path d="M42 20 H278 A22 22 0 0 0 300 42 V519 A22 22 0 0 0 278 541 H42 A22 22 0 0 0 20 519 V42 A22 22 0 0 0 42 20 Z" fill="none" stroke="#1a52a0" stroke-width="3"/>
      <path d="M44 26 H276 A18 18 0 0 0 294 44 V517 A18 18 0 0 0 276 535 H44 A18 18 0 0 0 26 517 V44 A18 18 0 0 0 44 26 Z" fill="none" stroke="#1a52a0" stroke-width="1.2"/>
    </svg>
    <div class="front-logo">
      <span class="dot"></span>
      <span class="name">harrowfields.net.au</span>
    </div>
    <h1 class="business-name">HARROWFIELD</h1>
    <svg class="ribbon" viewBox="0 0 180 46" aria-hidden="true">
      <path d="M2 10 H36 V34 H12 L20 22 Z" fill="#ffffff" stroke="#0a4179" stroke-width="3" stroke-linejoin="round"/>
      <path d="M178 10 H144 V34 H168 L160 22 Z" fill="#ffffff" stroke="#0a4179" stroke-width="3" stroke-linejoin="round"/>
      <path d="M26 4 Q90 -2 154 4 V30 Q90 24 26 30 Z" fill="#0a4179"/>
    </svg>
    <p class="ribbon-text">HORSE SUPPLIES</p>
    <p class="phone">1300 48 62 90</p>
    <div class="rule rule-top"></div>
    <p class="contact">orders@harrowfields.net.au<br>www.harrowfields.net.au</p>
    <div class="rule rule-bottom"></div>
    <p class="address">27 Lindqvist Rd Marrowbank<br>Q 4587</p>
  </section>

</main>
</body>
</html>
```